Business card design for holistic health care clinic

We need a double-sided business card design for our holistic health care clinic that integrates our logo design and also its color scheme. My business is called Valmira. It is an integrative medicine clinic. You have already done the logo for me. Please ensure an elegant and upscale design that is not cluttered, but still has all the necessary information (please see below for details).

Target Market(s)

Wellness, fitness, rehabilitation for educated, well-traveled open-minded clients who are focused on natural, organic, balanced and preventive healthcare and lifestyle.

Industry/Entity Type

Medical

Contact Information for Business Card

Modern, clean.

Number of Pages Required

1 page

Font styles to use
Serif
Sans Serif

Colors

Designer to choose colors to be used in the design.

Requirements
Must have
• Logo on one side, all other information on the other side.
• Other information should include:
• Tobias Wrenfeld - DOE, CPT, LMT
• 4100 East Marrow Drive
• Austin, TX 78119
• 512 555 0148
• 818 555 0192
• info@ValmiraHealth.example
• t.wrenfeld@ValmiraHealth.example
Nice to have
• Darker background on front - but not totally black - shaded/dark gray.

```html
<!DOCTYPE html>
<html lang="en">
<head>
<meta charset="utf-8">
<title>Valmira – Business Card</title>
<link rel="stylesheet" href="https://fonts.googleapis.com/css2?family=Open+Sans:wght@400;600;700&display=swap">
<style>
  :root {
    --backdrop: #3a312d;
    --card: #1f1f20;
    --card-edge: #2a2a2b;
    --accent: #1b8fd8;
    --text: #f2f2f2;
  }
  * { box-sizing: border-box; margin: 0; padding: 0; }
  html, body {
    width: 1200px;
    height: 844px;
    overflow: hidden;
    background: var(--backdrop);
    font-family: "Open Sans", Arial, sans-serif;
  }
  .stage {
    position: relative;
    width: 1200px;
    height: 844px;
  }
  .card {
    position: absolute;
    width: 525px;
    height: 300px;
    background: var(--card);
    border: 1px solid var(--card-edge);
    box-shadow: 0 14px 30px rgba(0,0,0,.45);
  }
  .card--info { left: 50px; top: 272px; }
  .card--logo { left: 625px; top: 272px; }

  .brand {
    position: absolute;
    text-align: left;
    color: var(--accent);
  }
  .brand__row {
    display: flex;
    align-items: center;
    gap: 10px;
  }
  .brand__dot {
    width: 16px;
    height: 16px;
    border-radius: 50%;
    background: var(--accent);
  }
  .brand__name {
    font-weight: 700;
    line-height: 1;
    letter-spacing: .5px;
  }
  .brand__tagline {
    font-weight: 600;
    margin-top: 4px;
  }

  .card--info .brand { right: 36px; top: 34px; }
  .card--info .brand__name { font-size: 46px; }
  .card--info .brand__tagline { font-size: 15px; }

  .card--logo .brand { left: 50%; top: 50%; transform: translate(-50%, -50%); }
  .card--logo .brand__name { font-size: 58px; }
  .card--logo .brand__tagline { font-size: 18px; }
  .card--logo .brand__dot { width: 20px; height: 20px; }

  .rule {
    position: absolute;
    left: 30px;
    right: 30px;
    height: 1.5px;
    background: var(--accent);
  }
  .rule--top { top: 128px; }
  .rule--bottom { top: 198px; }

  .holder {
    position: absolute;
    left: 30px;
    top: 160px;
    font-size: 17px;
    font-weight: 700;
    color: var(--accent);
  }
  .holder__credentials {
    font-size: 12px;
    font-weight: 600;
  }

  .contact {
    position: absolute;
    left: 30px;
    top: 212px;
    font-size: 12.5px;
    line-height: 24px;
    color: var(--text);
  }
  .contact__row span + span { margin-left: 14px; }
  .contact__email { color: var(--accent); }
</style>
</head>
<body>
<main class="stage">
  <section class="card card--info" aria-label="Business card, contact side">
    <div class="brand">
      <div class="brand__row">
        <span class="brand__dot"></span>
        <span class="brand__name">VALMIRA</span>
      </div>
      <div class="brand__tagline">Integrative Holistic Medicine</div>
    </div>
    <div class="rule rule--top"></div>
    <p class="holder">Tobias Wrenfeld <span class="holder__credentials">- DOE, CPT, LMT</span></p>
    <div class="rule rule--bottom"></div>
    <div class="contact">
      <p class="contact__row">4100 East Marrow Drive Austin, TX 78119</p>
      <p class="contact__row"><span>P- 512 555 0148</span><span>M- 818 555 0192</span><span>E- info@ValmiraHealth.example</span></p>
      <p class="contact__row contact__email">t.wrenfeld@ValmiraHealth.example</p>
    </div>
  </section>

  <section class="card card--logo" aria-label="Business card, logo side">
    <div class="brand">
      <div class="brand__row">
        <span class="brand__dot"></span>
        <span class="brand__name">VALMIRA</span>
      </div>
      <div class="brand__tagline">Integrative Holistic Medicine</div>
    </div>
  </section>
</main>
</body>
</html>
```